BrindleStaffing Business Card Design

We are a staffing company finding positions for dedicated nurses and physicians.

Target Market(s)

Business Professionals

Industry/Entity Type

Staffing

Contact Information for Business Card

Gordon Pratley
Chairman
417 39th Avenue South
SAINT PETERSBURG FL 33712
813-555-4172 Mobile
813-555-8036 Fax
gpratley@brindlestaffing.com
www.brindlestaffing.com

Font styles to use
Sans Serif

Colors
fbee3e
f04a50
f37122

Requirements
Must have
• Logo Attached, see colors below. We'd like to see Yellow, Orange and Red.

```html
<!DOCTYPE html>
<html lang="en">
<head>
<meta charset="utf-8">
<title>BrindleStaffing Business Card</title>
<link href="https://fonts.googleapis.com/css2?family=Poppins:wght@600&family=Questrial&display=swap" rel="stylesheet">
<style>
  :root {
    --page: #dcdcdc;
    --card: #e6e6e6;
    --yellow: #fbee3e;
    --orange: #f37122;
    --red: #f04a50;
    --accent: #f37122;
    --accent-2: #f04a50;
    --text: #555555;
    --rule: #6a6a6a;
    --band-1: #fbee3e;
    --band-2: #f9c934;
    --band-3: #f6a02b;
    --band-4: #f37122;
    --band-5: #f15c3a;
    --band-6: #f04a50;
    --white: #ffffff;
  }
  * { box-sizing: border-box; margin: 0; padding: 0; }
  html, body { width: 1200px; height: 1200px; overflow: hidden; background: var(--page); }
  .card {
    position: absolute;
    left: 227px;
    width: 745px;
    height: 425px;
    border-radius: 42px;
    overflow: hidden;
  }
  .card--front { top: 135px; background: var(--card); font-family: "Questrial", sans-serif; color: var(--text); }
  .card--back {
    top: 640px;
    background: linear-gradient(90deg, var(--band-1) 0%, var(--band-3) 28%, var(--band-4) 50%, var(--band-5) 75%, var(--band-6) 100%);
  }
  .brand {
    position: absolute;
    display: flex;
    align-items: center;
    gap: 12px;
    font-family: "Poppins", sans-serif;
    font-weight: 600;
    letter-spacing: -1.5px;
    line-height: 1;
  }
  .brand__dot { width: 16px; height: 16px; border-radius: 50%; flex: none; }
  .card--front .brand { left: 34px; top: 52px; font-size: 58px; color: var(--orange); }
  .card--front .brand__dot { background: var(--red); }
  .card--back .brand { left: 0; right: 0; top: 180px; justify-content: center; font-size: 60px; color: var(--white); }
  .card--back .brand__dot { background: var(--white); }
  .person { position: absolute; left: 34px; top: 208px; }
  .person__name { font-family: "Poppins", sans-serif; font-weight: 600; font-size: 22px; color: var(--orange); line-height: 1.2; }
  .person__name .surname { color: var(--red); }
  .person__title { font-size: 17px; line-height: 1.4; }
  .divider { position: absolute; left: 0; right: 0; top: 271px; height: 2px; background: var(--rule); }
  .divider__accent {
    position: absolute; left: 37px; top: 270px; width: 162px; height: 4px;
    background: radial-gradient(circle, var(--orange) 1px, var(--card) 1.3px) 0 0 / 5px 4px repeat-x;
  }
  .contact { position: absolute; left: 34px; top: 290px; list-style: none; font-size: 17px; line-height: 22.3px; }
  .contact li { display: flex; align-items: center; gap: 9px; }
  .contact svg { width: 16px; height: 16px; flex: none; fill: var(--accent); color: var(--accent); }
  .address { position: absolute; right: 34px; top: 337px; text-align: right; font-size: 17px; line-height: 22px; font-style: normal; }
  .band { position: absolute; left: 0; right: 0; bottom: 0; height: 24px; display: flex; }
  .band span { flex: 1; }
  .band span:nth-child(1) { background: var(--band-1); }
  .band span:nth-child(2) { background: var(--band-2); }
  .band span:nth-child(3) { background: var(--band-3); }
  .band span:nth-child(4) { background: var(--band-4); }
  .band span:nth-child(5) { background: var(--band-5); }
  .band span:nth-child(6) { background: var(--band-6); }
</style>
</head>
<body>
  <section class="card card--front">
    <div class="brand"><span>BrindleStaffing</span><span class="brand__dot"></span></div>
    <div class="person">
      <p class="person__name">Gordon <span class="surname">Pratley</span></p>
      <p class="person__title">Chairman</p>
    </div>
    <div class="divider"></div>
    <div class="divider__accent"></div>
    <ul class="contact">
      <li><svg viewBox="0 0 16 16" aria-hidden="true"><path d="M1 6c0-2 3-3.5 7-3.5S15 4 15 6v1.5h-3.5V6h-7v1.5H1z"/><path d="M3.5 8.5 5 6.5h6l1.5 2V14h-9z"/><circle cx="8" cy="10.5" r="1.8" fill="#e6e6e6"/></svg>813-555-4172</li>
      <li><svg viewBox="0 0 16 16" aria-hidden="true"><path d="M4 1h7v5H4z" fill="none" stroke="currentColor" stroke-width="1.4"/><path d="M1 6h14v8H1zM2.5 7.5v5h2v-5z"/><rect x="6" y="8" width="7" height="1.2" fill="#e6e6e6"/><rect x="6" y="10.5" width="7" height="1.2" fill="#e6e6e6"/></svg>813-555-8036</li>
      <li><svg viewBox="0 0 16 16" aria-hidden="true"><path d="M1 3.5h14v9H1z" fill="none" stroke="currentColor" stroke-width="1.4"/><path d="M1.5 4 8 9l6.5-5" fill="none" stroke="currentColor" stroke-width="1.4"/></svg>gpratley@brindlestaffing.com</li>
      <li><svg viewBox="0 0 16 16" aria-hidden="true"><circle cx="8" cy="8" r="7"/><path d="M4 4c2 0 2 2 4 2s1 3-1 3-2 3-3 3-1-2-1-4 1-4 1-4zM10 10c1 0 2 1 2 2l-2 1z" fill="#e6e6e6"/></svg>www.brindlestaffing.com</li>
    </ul>
    <address class="address">417 39th Avenue South<br>SAINT PETERSBURG FL 33712</address>
    <div class="band"><span></span><span></span><span></span><span></span><span></span><span></span></div>
  </section>

  <section class="card card--back">
    <div class="brand"><span>BrindleStaffing</span><span class="brand__dot"></span></div>
  </section>
</body>
</html>
```